Card design for orthopaedic surgeons working as The Brightwater Joint Centre

Business cards, letterhead

Colors

Designer to choose colors to be used in the design.

Requirements
Must have
• Late addition.
• Cards letterhead must have logos of
• Crestmoor Lindell College of Surgeons
• Varenwood Bone Health Association
Nice to have
• Back of card to have space for appointment time to be added by hand and some blank space for writing incidental other notes.

```html
<!DOCTYPE html>
<html lang="en">
<head>
<meta charset="utf-8">
<title>The Brightwater Joint Centre – Business Card</title>
<link rel="stylesheet" href="https://fonts.googleapis.com/css2?family=Montserrat:wght@400&family=Roboto:wght@400;700&display=swap">
<style>
  :root {
    --navy: #04334d;
    --sky: #4fa6dc;
    --white: #ffffff;
    --backdrop: #b9b9b9;
  }
  * { margin: 0; padding: 0; box-sizing: border-box; }
  html, body { width: 1172px; height: 1200px; overflow: hidden; }
  body { background: var(--backdrop); position: relative; font-family: "Roboto", Arial, sans-serif; }

  .card {
    position: absolute;
    left: 214px;
    width: 744px;
    height: 428px;
    border-radius: 28px;
    overflow: hidden;
  }
  .card--front { top: 122px; background: var(--navy); }
  .card--back { top: 645px; background: var(--white); }

  .wordmark {
    position: absolute;
    left: 0; right: 0;
    text-align: center;
    font-family: "Montserrat", Arial, sans-serif;
    font-weight: 400;
    font-size: 43px;
    letter-spacing: -1px;
    line-height: 1;
    white-space: nowrap;
  }
  .card--front .wordmark { top: 213px; color: var(--white); }
  .card--back .wordmark { top: 131px; color: var(--navy); }

  .person {
    position: absolute;
    right: 392px;
    top: 249px;
    text-align: right;
    white-space: nowrap;
  }
  .person__name { font-weight: 700; font-size: 29px; color: var(--sky); letter-spacing: -0.3px; line-height: 1.2; }
  .person__role { font-size: 20px; color: var(--navy); margin-top: 2px; }

  .divider {
    position: absolute;
    left: 376px; top: 240px;
    width: 2px; height: 80px;
    background: var(--navy);
  }

  .contacts { position: absolute; left: 399px; top: 237px; list-style: none; white-space: nowrap; }
  .contacts li {
    display: flex; align-items: center;
    height: 30px;
    font-size: 21px; color: var(--navy);
  }
  .contacts svg { width: 15px; height: 15px; margin-right: 9px; fill: var(--sky); flex: none; }

  .wave { position: absolute; left: 0; bottom: 0; width: 744px; height: 430px; }
</style>
</head>
<body>
  <section class="card card--front">
    <p class="wordmark">The Brightwater Joint Centre</p>
  </section>

  <section class="card card--back">
    <p class="wordmark">The Brightwater Joint Centre</p>

    <div class="person">
      <p class="person__name">Dr. Elliot Marsh</p>
      <p class="person__role">Orthopaedic Specialist</p>
    </div>

    <div class="divider"></div>

    <ul class="contacts">
      <li>
        <svg viewBox="0 0 24 24" aria-hidden="true"><path d="M6.6 10.8a15.1 15.1 0 0 0 6.6 6.6l2.2-2.2a1 1 0 0 1 1-.25 11.4 11.4 0 0 0 3.6.57 1 1 0 0 1 1 1V20a1 1 0 0 1-1 1A17 17 0 0 1 3 4a1 1 0 0 1 1-1h3.5a1 1 0 0 1 1 1c0 1.25.2 2.45.57 3.57a1 1 0 0 1-.25 1z"/></svg>
        555-204-7318
      </li>
      <li>
        <svg viewBox="0 0 24 24" aria-hidden="true"><path d="M2 5h20v14H2z"/><path d="M3.5 6.5 12 13l8.5-6.5" fill="none" stroke="#fff" stroke-width="2"/></svg>
        info@brightwaterjoint.com
      </li>
      <li>
        <svg viewBox="0 0 24 24" aria-hidden="true"><circle cx="12" cy="12" r="10"/><path d="M8 6c2 1 1 3 3 4s-1 3 1 5-2 4-2 4M15 5c-1 2 2 3 3 5s-2 3 1 5" fill="none" stroke="#fff" stroke-width="1.5"/></svg>
        www.brightwaterjoint.com
      </li>
    </ul>

    <svg class="wave" viewBox="0 0 1209 698" preserveAspectRatio="none" aria-hidden="true">
      <path d="M0 644 C200 540 400 565 600 612 C850 668 1050 690 1209 618 L1209 698 L0 698 Z" fill="#04334d"/>
      <path d="M530 592 C800 650 1050 680 1209 568 L1209 598 C1050 680 800 660 530 592 Z" fill="#4fa6dc"/>
    </svg>
  </section>
</body>
</html>
```